Lanternfield Drinks business cards

We need a business card design for our new logo. The company is modern, progressive, professional, yet approachable. The key products are ready to drink bottles and cans of coffee based beverages.
These cards will be a critical part of the first impression made by our sales organization, business development team, and all external facing personnel.
Card can be a vertical or horizontal orientation.

Target Market(s)

Customers, suppliers, business partners

Industry/Entity Type

Business

Contact Information for Business Card

Business cards should feature Company Name and Logo.

Font styles to use
Serif

Colors

Designer to choose colors to be used in the design.

Requirements
Must have
• Strong readability of Name, phone #, mobile number and email address.
• Job title, website url, Street Address, and other details can be secondary level readability.
Nice to have
• High impact, simplistic quality design.
• Ok to utilize the 'H in the box' separate from the company name

```html
<!DOCTYPE html>
<html lang="en">
<head>
<meta charset="utf-8">
<title>Lanternfield Drinks – Business Cards</title>
<link rel="stylesheet" href="https://fonts.googleapis.com/css2?family=Crimson+Pro:wght@400;600;700&display=swap">
<style>
  :root {
    --backdrop: #9b9b9b;
    --brand-orange: #e1532a;
    --brand-orange-deep: #d24a24;
    --ink: #333333;
    --rule-grey: #9a9a9a;
    --band-grey: #8c8c8c;
    --paper: #ffffff;
    --paper-shade: #ececec;
  }
  * { box-sizing: border-box; margin: 0; padding: 0; }
  html, body { width: 1200px; height: 900px; overflow: hidden; }
  body {
    background: var(--backdrop);
    font-family: "Crimson Pro", Georgia, serif;
    position: relative;
  }
  .card {
    position: absolute;
    width: 600px;
    height: 343px;
    border-radius: 18px;
    overflow: hidden;
    box-shadow: 0 6px 14px rgba(0,0,0,0.28);
  }

  /* Back of card */
  .card-back {
    left: 110px;
    top: 80px;
    background: linear-gradient(135deg, var(--brand-orange-deep), var(--brand-orange));
  }
  .card-back .faint-square {
    position: absolute;
    left: 330px;
    top: 30px;
    width: 230px;
    height: 230px;
    border: 14px solid rgba(255,255,255,0.13);
    outline: 6px solid rgba(255,255,255,0.08);
    outline-offset: 10px;
  }
  .card-back .brand {
    position: absolute;
    left: 0; right: 0; top: 0; bottom: 0;
    display: flex;
    align-items: center;
    justify-content: center;
    gap: 18px;
  }
  .brand-square {
    width: 62px;
    height: 62px;
    border: 4px solid currentColor;
    flex: none;
  }
  .card-back .brand { color: var(--paper); }
  .brand-name {
    font-weight: 600;
    font-size: 44px;
    letter-spacing: 1px;
    line-height: 1;
    text-transform: uppercase;
  }

  /* Front of card */
  .card-front {
    left: 490px;
    top: 460px;
    background: linear-gradient(160deg, var(--paper) 40%, var(--paper-shade));
  }
  .card-front .brand {
    position: absolute;
    left: 34px;
    top: 34px;
    display: flex;
    align-items: center;
    gap: 14px;
    color: var(--brand-orange);
  }
  .card-front .brand-square { width: 50px; height: 50px; border-width: 3px; }
  .card-front .brand-name { font-size: 34px; }
  .top-rule {
    position: absolute;
    left: 300px; right: 20px; top: 40px;
    height: 1px;
    background: var(--rule-grey);
  }
  .person {
    position: absolute;
    left: 40px;
    top: 118px;
  }
  .person-name {
    font-size: 34px;
    font-weight: 600;
    color: var(--brand-orange);
    line-height: 1;
  }
  .person-title {
    font-size: 22px;
    color: var(--ink);
    margin-top: 2px;
  }
  .mid-rule {
    position: absolute;
    left: 40px; right: 40px; top: 190px;
    height: 1px;
    background: var(--rule-grey);
  }
  .contacts {
    position: absolute;
    left: 40px;
    top: 202px;
    list-style: none;
    font-size: 19px;
    color: var(--ink);
    line-height: 27px;
  }
  .contacts li { display: flex; align-items: center; gap: 10px; }
  .contacts svg { width: 15px; height: 15px; fill: var(--brand-orange); flex: none; }
  .address {
    position: absolute;
    right: 30px;
    top: 210px;
    text-align: right;
    font-size: 17px;
    line-height: 21px;
    color: var(--ink);
  }
  .footer-band {
    position: absolute;
    left: 0; bottom: 0;
    width: 600px; height: 70px;
  }
  .website {
    position: absolute;
    right: 28px;
    bottom: 16px;
    font-size: 17px;
    color: var(--paper);
  }
</style>
</head>
<body>

  <section class="card card-back" aria-label="Card back">
    <div class="faint-square"></div>
    <div class="brand">
      <div class="brand-square"></div>
      <div class="brand-name">Lanternfield Drinks</div>
    </div>
  </section>

  <section class="card card-front" aria-label="Card front">
    <div class="brand">
      <div class="brand-square"></div>
      <div class="brand-name">Lanternfield Drinks</div>
    </div>
    <div class="top-rule" style="top:100px;left:300px;"></div>

    <div class="person">
      <div class="person-name">Daniel Ward</div>
      <div class="person-title">President</div>
    </div>
    <div class="mid-rule"></div>

    <ul class="contacts">
      <li>
        <svg viewBox="0 0 24 24" aria-hidden="true"><path d="M6.6 10.8a15 15 0 0 0 6.6 6.6l2.2-2.2a1 1 0 0 1 1-.25 11.4 11.4 0 0 0 3.6.57 1 1 0 0 1 1 1V20a1 1 0 0 1-1 1A17 17 0 0 1 3 4a1 1 0 0 1 1-1h3.5a1 1 0 0 1 1 1c0 1.25.2 2.45.57 3.57a1 1 0 0 1-.25 1z"/></svg>
        555 301 4420
      </li>
      <li>
        <svg viewBox="0 0 24 24" aria-hidden="true"><path d="M7 1h10a2 2 0 0 1 2 2v18a2 2 0 0 1-2 2H7a2 2 0 0 1-2-2V3a2 2 0 0 1 2-2zm0 3v14h10V4zm5 15.2a1 1 0 1 0 0 2 1 1 0 0 0 0-2z"/></svg>
        555 301 4421
      </li>
      <li>
        <svg viewBox="0 0 24 24" aria-hidden="true"><path d="M2 5h20v14H2zm2 2v.4l8 5 8-5V7zm0 2.8V17h16V9.8l-8 5z"/></svg>
        info@lanternfielddrinks.com
      </li>
    </ul>

    <address class="address" style="font-style:normal;">
      Level 2, 17 Harbour Lane<br>
      Eastbay, VIC 3100
    </address>

    <svg class="footer-band" viewBox="0 0 600 70" aria-hidden="true">
      <path d="M0,49 L398,49 C418,49 424,13 446,11 L600,11 L600,70 L0,70 Z" fill="var(--band-grey)"/>
      <path d="M0,56 L404,56 C424,56 430,20 452,18 L600,18 L600,70 L0,70 Z" fill="var(--brand-orange)"/>
    </svg>
    <div class="website">www.lanternfielddrinks.com</div>
  </section>

</body>
</html>
```